kelvaro stationary business card and letterhead

THIS PROJECT IS TO DESIGN A BUSINESS CARD DOUBLE SIDES .

Reason: I AM WAITING FOR TESINU SUBMISION

Industry/Entity Type

Business

Font styles to use
Other font styles liked:
• Chose your font

```html
<!DOCTYPE html>
<html lang="en">
<head>
<meta charset="utf-8">
<title>kelvaro stationery – letterhead and business cards</title>
<link rel="stylesheet" href="https://fonts.googleapis.com/css2?family=Open+Sans:wght@400;600&display=swap">
<style>
  :root {
    --ink: #2b2a29;
    --charcoal: #2d2c2b;
    --gold: #f2bb16;
    --paper: #ffffff;
    --backdrop: #ececec;
    --body-text: #3a3a3a;
    --contact-text: #e8e8e8;
  }
  * { box-sizing: border-box; margin: 0; padding: 0; }
  html, body { width: 1200px; height: 1000px; overflow: hidden; }
  body {
    background: var(--backdrop);
    font-family: "Open Sans", Arial, sans-serif;
    color: var(--ink);
    position: relative;
  }

  /* brand lockup */
  .brand { display: flex; align-items: center; gap: 8px; }
  .brand-dot { width: 22px; height: 22px; border-radius: 50%; background: var(--gold); flex: none; }
  .brand-text { display: flex; flex-direction: column; line-height: 1; }
  .brand-name { font-weight: 600; font-size: 22px; letter-spacing: 2px; text-transform: uppercase; color: var(--ink); }
  .brand-tagline { font-size: 7px; letter-spacing: 1.4px; text-transform: uppercase; color: var(--gold); margin-top: 3px; }

  /* letterhead */
  .letterhead {
    position: absolute; left: 60px; top: 60px;
    width: 560px; height: 792px;
    background: var(--paper);
    box-shadow: 0 2px 8px rgba(0,0,0,.12);
    overflow: hidden;
  }
  .letterhead .brand { position: absolute; top: 56px; left: 50%; transform: translateX(-50%); }
  .letter-body {
    position: absolute; left: 70px; right: 70px; top: 160px;
    font-size: 9px; line-height: 1.6; color: var(--body-text);
  }
  .letter-body p { margin-bottom: 16px; }
  .letter-salutation { margin-bottom: 6px !important; }
  .signature {
    width: 110px; height: 34px; margin: 8px 0 20px auto;
    background: linear-gradient(90deg, #f4f4f4, #e6e6e6);
    border-radius: 4px;
  }
  .letter-closing { margin-top: 10px; }

  .letter-footer { position: absolute; left: 0; right: 0; bottom: 0; height: 96px; }
  .letter-footer .contact-tab {
    position: absolute; right: 0; top: 0; width: 250px; height: 56px;
    background: var(--charcoal); border-top: 3px solid var(--gold);
    padding: 8px 16px; display: flex; justify-content: space-between;
  }
  .letter-footer .base-band {
    position: absolute; left: 0; right: 0; bottom: 0; height: 40px; background: var(--charcoal);
  }
  .letter-footer .gold-block {
    position: absolute; left: 0; bottom: 0; width: 70px; height: 40px; background: var(--gold);
  }
  .letter-footer .gold-block span {
    position: absolute; left: 22px; top: 8px; width: 24px; height: 24px;
    border-radius: 50%; background: var(--charcoal);
  }

  .contact-list { list-style: none; font-size: 7px; color: var(--contact-text); line-height: 1.7; }
  .contact-list li { display: flex; align-items: center; gap: 4px; white-space: nowrap; }
  .contact-list svg { width: 7px; height: 7px; flex: none; }

  /* business cards */
  .card {
    position: absolute; width: 440px; height: 250px;
    box-shadow: 0 2px 8px rgba(0,0,0,.14);
    overflow: hidden;
  }
  .card-back { left: 700px; top: 170px; background: var(--paper); }
  .card-back .brand { position: absolute; left: 34px; top: 50px; }
  .card-holder { position: absolute; left: 34px; top: 128px; }
  .card-holder-name { font-size: 20px; color: var(--ink); }
  .card-holder-role { font-size: 9px; color: var(--gold); margin-top: 2px; }
  .card-back .gold-rule {
    position: absolute; right: 0; top: 70px; width: 230px; height: 3px; background: var(--gold);
  }
  .card-back .bottom-band {
    position: absolute; left: 0; right: 0; bottom: 0; height: 42px;
    background: var(--charcoal); z-index: 1;
  }
  .card-back .contact-panel {
    position: absolute; right: 0; top: 73px; width: 230px; height: 177px;
    background: var(--charcoal); z-index: 2;
    clip-path: polygon(30% 0, 100% 0, 100% 100%, 0 100%, 0 72%);
  }
  .card-back .contact-list { position: absolute; right: 18px; font-size: 8px; }
  .card-back .contact-list.phones { top: 12px; }
  .card-back .contact-list.online { bottom: 10px; }

  .card-front { left: 700px; top: 580px; background: var(--charcoal); display: flex; align-items: center; justify-content: center; }
  .card-front .brand-name { color: #f5f5f5; font-size: 28px; }
  .card-front .brand-tagline { font-size: 9px; }
  .card-front .brand-dot { width: 28px; height: 28px; }
</style>
</head>
<body>

<article class="letterhead">
  <div class="brand">
    <span class="brand-dot"></span>
    <div class="brand-text">
      <span class="brand-name">kelvaro</span>
      <span class="brand-tagline">International Consulting</span>
    </div>
  </div>

  <div class="letter-body">
    <p class="letter-salutation">Dear Client</p>
    <p>Lorem ipsum dolor sit amet, consectetur adipiscing elit. Nulla sodales nisi vitae ipsum tempor, sed feugiat eros facilisis. Aliquam mauris enim, fermentum eu lacinia sit amet, laoreet nec odio.</p>
    <p>Nullam aliquam ligula ac sem aliquet varius. Fusce ultricies lobortis odio, quis porttitor sapien interdum at. Integer turpis nunc, posuere at quam vel, consequat tincidunt felis.</p>
    <div class="signature" role="img" aria-label="Handwritten signature of Marin Oster"></div>
    <p>Pellentesque habitant morbi tristique senectus et netus et malesuada fames. Donec quis fermentum massa, vel iaculis elit.</p>
    <p class="letter-closing">Best regards,</p>
  </div>

  <footer class="letter-footer">
    <div class="contact-tab">
      <ul class="contact-list">
        <li><svg viewBox="0 0 8 8"><rect x="0.5" y="1.5" width="7" height="5" fill="none" stroke="#f2bb16"/><path d="M0.5 1.5 4 4.5 7.5 1.5" fill="none" stroke="#f2bb16"/></svg>hello@kelvaro-consult.com</li>
        <li><svg viewBox="0 0 8 8"><circle cx="4" cy="4" r="3.4" fill="none" stroke="#f2bb16"/><path d="M0.6 4h6.8M4 0.6v6.8" stroke="#f2bb16" stroke-width=".7"/></svg>www.kelvaro-consult.com</li>
      </ul>
      <ul class="contact-list">
        <li><svg viewBox="0 0 8 8"><path d="M1.5 0.8 3 2.5 2.2 3.5Q3.3 5 4.5 5.8L5.5 5 7.2 6.5 6.3 7.5Q3 6.5 0.6 1.8Z" fill="#f2bb16"/></svg>555-0142-78</li>
        <li><svg viewBox="0 0 8 8"><rect x="1" y="1" width="6" height="6" fill="#f2bb16"/></svg>555-0142-79</li>
        <li><svg viewBox="0 0 8 8"><rect x="1" y="1" width="6" height="6" fill="#f2bb16"/></svg>555-0142-80</li>
      </ul>
    </div>
    <div class="base-band"></div>
    <div class="gold-block"><span></span></div>
  </footer>
</article>

<section class="card card-back">
  <div class="brand">
    <span class="brand-dot"></span>
    <div class="brand-text">
      <span class="brand-name">kelvaro</span>
      <span class="brand-tagline">International Consulting</span>
    </div>
  </div>
  <div class="card-holder">
    <div class="card-holder-name">Marin Oster</div>
    <div class="card-holder-role">Managing Director</div>
  </div>
  <div class="gold-rule"></div>
  <div class="bottom-band"></div>
  <div class="contact-panel">
    <ul class="contact-list phones">
      <li><svg viewBox="0 0 8 8"><path d="M1.5 0.8 3 2.5 2.2 3.5Q3.3 5 4.5 5.8L5.5 5 7.2 6.5 6.3 7.5Q3 6.5 0.6 1.8Z" fill="#f2bb16"/></svg>555-0142-78</li>
      <li><svg viewBox="0 0 8 8"><rect x="1" y="1" width="6" height="6" fill="#f2bb16"/></svg>555-0142-79</li>
      <li><svg viewBox="0 0 8 8"><rect x="1" y="1" width="6" height="6" fill="#f2bb16"/></svg>555-0142-80</li>
    </ul>
    <ul class="contact-list online">
      <li><svg viewBox="0 0 8 8"><rect x="0.5" y="1.5" width="7" height="5" fill="none" stroke="#f2bb16"/><path d="M0.5 1.5 4 4.5 7.5 1.5" fill="none" stroke="#f2bb16"/></svg>hello@kelvaro-consult.com</li>
      <li><svg viewBox="0 0 8 8"><circle cx="4" cy="4" r="3.4" fill="none" stroke="#f2bb16"/><path d="M0.6 4h6.8M4 0.6v6.8" stroke="#f2bb16" stroke-width=".7"/></svg>www.kelvaro-consult.com</li>
    </ul>
  </div>
</section>

<section class="card card-front">
  <div class="brand">
    <span class="brand-dot"></span>
    <div class="brand-text">
      <span class="brand-name">kelvaro</span>
      <span class="brand-tagline">International Consulting</span>
    </div>
  </div>
</section>

</body>
</html>
```